Home Remodeling company needs a business card design

we need a business card design for home remodeling company in hamilton county, indiana USA. we offers a wide range of construction services including whole house renovations, Design and Build Basements and Kitchen and Bathroom Remodeling . we would like to see designs for both site of business card that use the same color of the company logo and also including all information below :
1- Karim Feltous CEO / General Contractor
2- all company contacts Telephone numbers ( 1-888-DULOM-47 ) ( 317-555-0193) email address ( info@dulomhome.com) website ( www.dulomhome.com ) and social media logos (Facebook- twitter- google plus )
3- company logo
4- licensed . insured . bonded

```html
<!DOCTYPE html>
<html lang="en">
<head>
<meta charset="UTF-8">
<title>Dulom Home Remodeling – Business Card</title>
<link href="https://fonts.googleapis.com/css2?family=Poppins:wght@700&family=Raleway:wght@300;400;500&display=swap" rel="stylesheet">
<style>
  :root {
    --bg: #e6e7ea;
    --paper: #ffffff;
    --ink: #0b0b0b;
    --logo-grey: #3a3a3c;
    --accent-red: #c8202b;
    --muted: #8a8a8c;
    --on-dark: #e8e8e8;
    --social-1: #3b5b98;
    --social-2: #2aa3e0;
    --social-3: #d34836;
  }
  * { box-sizing: border-box; margin: 0; padding: 0; }
  html, body { width: 1200px; height: 900px; overflow: hidden; }
  body {
    background: var(--bg);
    font-family: "Raleway", sans-serif;
    position: relative;
  }
  .card {
    position: absolute;
    left: 290px;
    width: 620px;
    height: 354px;
    background: var(--paper);
    box-shadow: 0 10px 28px rgba(0,0,0,.16);
    overflow: hidden;
  }
  .card--back { top: 70px; }
  .card--front { top: 470px; }

  /* logo block */
  .brand { display: flex; flex-direction: column; align-items: flex-start; }
  .brand__row { display: flex; align-items: center; gap: 12px; }
  .brand__mark { width: 14px; height: 14px; background: var(--accent-red); }
  .brand__name {
    font-family: "Poppins", sans-serif;
    font-weight: 700;
    font-size: 62px;
    line-height: 1;
    letter-spacing: 2px;
    color: var(--logo-grey);
  }
  .brand__tagline {
    margin-left: 28px;
    font-family: "Raleway", sans-serif;
    font-weight: 500;
    font-size: 15px;
    letter-spacing: 6.4px;
    color: var(--muted);
    text-transform: uppercase;
  }

  /* back card */
  .card--back .band-top { position: absolute; left: 0; top: 0; width: 100%; height: 82px; background: var(--ink); }
  .card--back .band-bottom { position: absolute; left: 0; bottom: 0; width: 100%; height: 118px; background: var(--ink); }
  .card--back .brand { position: absolute; left: 50%; top: 104px; transform: translateX(-50%); }

  /* front card */
  .card--front .brand { position: absolute; left: 50%; top: 52px; transform: translateX(-50%); }
  .credentials {
    position: absolute; left: 0; right: 0; top: 166px;
    text-align: center;
    font-weight: 300; font-size: 13px; letter-spacing: 2.5px;
    color: var(--muted);
  }
  .info-band {
    position: absolute; left: 0; bottom: 0; width: 100%; height: 140px;
    background: var(--ink); color: var(--on-dark);
  }
  .person { position: absolute; left: 44px; top: 56px; }
  .person__name { font-weight: 400; font-size: 21px; letter-spacing: .5px; }
  .person__role { font-weight: 300; font-size: 11px; margin-top: 4px; letter-spacing: .4px; }
  .divider { position: absolute; left: 330px; top: 26px; width: 1px; height: 88px; background: #8d8d8d; }
  .contacts { position: absolute; left: 356px; top: 38px; list-style: none; }
  .contacts li { display: flex; align-items: center; gap: 10px; font-size: 12px; font-weight: 400; height: 22px; letter-spacing: .3px; }
  .contacts svg { width: 12px; height: 12px; flex: none; }
  .social { position: absolute; right: 22px; top: 14px; display: flex; gap: 5px; }
  .social span { width: 14px; height: 14px; display: block; }
  .social .s1 { background: var(--social-1); }
  .social .s2 { background: var(--social-2); }
  .social .s3 { background: var(--social-3); }
</style>
</head>
<body>

  <section class="card card--back" aria-label="Business card, logo side">
    <div class="band-top"></div>
    <div class="brand">
      <div class="brand__row"><span class="brand__mark"></span><span class="brand__name">DULOM</span></div>
      <span class="brand__tagline">Home Remodeling</span>
    </div>
    <div class="band-bottom"></div>
  </section>

  <section class="card card--front" aria-label="Business card, contact side">
    <div class="brand">
      <div class="brand__row"><span class="brand__mark"></span><span class="brand__name">DULOM</span></div>
      <span class="brand__tagline">Home Remodeling</span>
    </div>
    <p class="credentials">licensed . insured . bonded</p>

    <div class="info-band">
      <div class="social" aria-label="Social media">
        <span class="s1"></span><span class="s2"></span><span class="s3"></span>
      </div>
      <div class="person">
        <p class="person__name">Karim Feltous</p>
        <p class="person__role">CEO / General Contractor</p>
      </div>
      <div class="divider"></div>
      <ul class="contacts">
        <li>
          <svg viewBox="0 0 24 24" aria-hidden="true"><path fill="#e8e8e8" d="M6.6 10.8a15 15 0 0 0 6.6 6.6l2.2-2.2c.3-.3.7-.4 1-.2 1.1.4 2.3.6 3.6.6.6 0 1 .4 1 1V20c0 .6-.4 1-1 1A17 17 0 0 1 3 4c0-.6.4-1 1-1h3.5c.6 0 1 .4 1 1 0 1.3.2 2.5.6 3.6.1.3 0 .7-.2 1z"/></svg>
          1-888-DULOM-47 | 317-555-0193
        </li>
        <li>
          <svg viewBox="0 0 24 24" aria-hidden="true"><g fill="none" stroke="#e8e8e8" stroke-width="2"><circle cx="12" cy="12" r="9"/><path d="M3 12h18M12 3c3 3.5 3 14.5 0 18M12 3c-3 3.5-3 14.5 0 18"/></g></svg>
          www.dulomhome.com
        </li>
        <li>
          <svg viewBox="0 0 24 24" aria-hidden="true"><g fill="none" stroke="#e8e8e8" stroke-width="2"><rect x="3" y="5" width="18" height="14"/><path d="M3 6l9 7 9-7"/></g></svg>
          info@dulomhome.com
        </li>
      </ul>
    </div>
  </section>

</body>
</html>
```